Quiet Horizons: Consequences of Aerial Anomalies for Culture, Religious Devotion, and Personal Thought.

Book cover, spine, and back cover. This is written by Dr. T. HALLORAN, and will be an educational book for academics, government officials, and the general population.
I'm imagining the outline of a person with am active mind in the middle. It would be overlayed on top of a circular galaxy on the background. On either side, smaller, perhaps in the background would be a cross on one side and a few uaps (ufo) of different shapes on the other (orb, saucer, triangle. ) beneath allnof this would be something symbolizing society - either the earth itself or the skyline of a large city.
By Dr. T. HALLORAN along the bottom, i presume. (Ai cannot make this, but I've included a few examples nonetheless. )
I assume I will be given the opportunity to write a synopsis on the back cover. I will be self publishing and selling from my website.
Academics, professionals, church leaders, government officials, and the general public.
Professional and community education
- It should look like a ph.d level book. Eye catching but not overly fantastical. (Its an educational book not a comic book)
- Not hollywood or fantasy book looking. It should look a graduate school book. The tone is quite serious.

```html
<!DOCTYPE html>
<html lang="en">
<head>
<meta charset="utf-8">
<title>Quiet Horizons — Full Cover Layout</title>
<link href="https://fonts.googleapis.com/css2?family=Cinzel:wght@400;500&family=Montserrat:wght@400&display=swap" rel="stylesheet">
<style>
  :root {
    --page-bg: #ffffff;
    --cover-black: #050507;
    --spine-black: #0b0b0e;
    --ink-light: #ffffff;
    --ink-soft: #e6e8ee;
    --galaxy-deep: #0d1a3c;
    --galaxy-mid: #2a4a8f;
    --galaxy-glow: #c98a4a;
    --earth-blue: #3a7fd9;
  }
  * { margin: 0; padding: 0; box-sizing: border-box; }
  html, body {
    width: 1200px; height: 1200px; overflow: hidden;
    background: var(--page-bg);
  }
  .cover-wrap {
    position: absolute; left: 91px; top: 237px;
    width: 1025px; height: 733px;
    display: flex;
    background: var(--cover-black);
  }
  .back-cover {
    position: relative; width: 489px; height: 100%;
    background: radial-gradient(ellipse at 50% 20%, #111218 0%, var(--cover-black) 60%);
    color: var(--ink-light);
  }
  .back-title {
    position: absolute; top: 30px; left: 0; width: 100%;
    text-align: center;
    font-family: "Cinzel", serif; font-weight: 400;
    font-size: 50px; line-height: 58px; letter-spacing: 0.08em;
  }
  .back-subtitle {
    position: absolute; top: 157px; left: 27px; width: 437px;
    text-align: center;
    font-family: "Cinzel", serif; font-weight: 500;
    font-size: 12px; line-height: 19px; letter-spacing: 0.03em;
  }
  .synopsis {
    position: absolute; top: 218px; left: 27px; width: 437px;
    font-family: "Montserrat", sans-serif;
    font-size: 10px; line-height: 15.8px; text-align: justify;
    color: var(--ink-soft);
  }
  .synopsis p + p { margin-top: 15.8px; }
  .isbn-box {
    position: absolute; left: 291px; top: 623px;
    width: 170px; height: 76px; background: #ffffff;
  }
  .spine {
    position: relative; width: 48px; height: 100%;
    background: var(--spine-black);
    color: var(--ink-light);
    font-family: "Cinzel", serif;
  }
  .spine-title, .spine-author {
    position: absolute; left: 50%;
    writing-mode: vertical-rl;
    transform: translateX(-50%);
    white-space: nowrap;
  }
  .spine-title { top: 36px; font-size: 29px; letter-spacing: 0.05em; }
  .spine-author { top: 540px; font-size: 21px; letter-spacing: 0.04em; }
  .front-cover {
    position: relative; width: 488px; height: 100%;
    background: var(--cover-black); overflow: hidden;
    color: var(--ink-light);
  }
  .front-art {
    position: absolute; left: 0; top: 210px; width: 100%; height: 523px;
    background:
      radial-gradient(ellipse 130% 40% at 50% 100%, var(--earth-blue) 0%, #10204a 30%, transparent 55%),
      radial-gradient(circle at 52% 42%, var(--galaxy-glow) 0%, #7a5a8a 12%, var(--galaxy-mid) 28%, var(--galaxy-deep) 52%, var(--cover-black) 80%);
  }
  .front-title {
    position: absolute; top: 22px; left: 0; width: 100%;
    text-align: center;
    font-family: "Cinzel", serif; font-weight: 400;
    font-size: 66px; line-height: 86px; letter-spacing: 0.07em;
  }
  .front-subtitle {
    position: absolute; top: 208px; left: 22px; width: 444px;
    text-align: center;
    font-family: "Cinzel", serif; font-weight: 500;
    font-size: 12.5px; line-height: 19px; letter-spacing: 0.03em;
  }
  .front-author {
    position: absolute; top: 668px; left: 0; width: 100%;
    text-align: center;
    font-family: "Cinzel", serif; font-weight: 400;
    font-size: 33px; letter-spacing: 0.05em;
  }
</style>
</head>
<body>
  <main class="cover-wrap">
    <section class="back-cover">
      <h2 class="back-title">QUIET<br>HORIZONS</h2>
      <p class="back-subtitle">CONSEQUENCES OF AERIAL ANOMALIES FOR CULTURE, RELIGIOUS DEVOTION, AND PERSONAL THOUGHT.</p>
      <div class="synopsis">
        <p>Lorem Ipsum is simply dummy text of the printing and typesetting industry. Lorem Ipsum has been the industry's standard dummy text ever since the 1500s, when an unknown printer took a galley of type and scrambled it to make a type specimen book. It has survived not only five centuries, but also the leap</p>
        <p>into electronic typesetting, remaining essentially unchanged. It was popularised in the 1960s with the release of Drytype sheets containing Lorem Ipsum passages, and more recently with desktop publishing software like Quillset Layout including versions of Lorem Ipsum. simply dummy text of the printing and.</p>
        <p>typesetting industry. Lorem Ipsum has been the industry's standard dummy text ever since the 1500s, when an unknown printer took a galley of type and scrambled it to make a type specimen book. It has survived not only five centuries, but also the leap into electronic typesetting,</p>
        <p>remaining essentially unchanged. It was popularised in the 1960s with the release of Drytype sheets containing Lorem Ipsum passages, and more recently with desktop publishing software like Quillset Layout including versions of Lorem Ipsum.</p>
      </div>
      <div class="isbn-box"></div>
    </section>
    <section class="spine">
      <span class="spine-title">QUIET HORIZONS</span>
      <span class="spine-author">DR. T. HALLORAN</span>
    </section>
    <section class="front-cover">
      <div class="front-art" role="img" aria-label="Silhouette of a human head with a glowing brain over a spiral galaxy, a glowing cross on one side, a saucer, orb and triangle craft on the other, above the curve of the Earth with a lit city skyline"></div>
      <h1 class="front-title">QUIET<br>HORIZONS</h1>
      <p class="front-subtitle">CONSEQUENCES OF AERIAL ANOMALIES FOR CULTURE, RELIGIOUS DEVOTION, AND PERSONAL THOUGHT.</p>
      <p class="front-author">DR. T. HALLORAN</p>
    </section>
  </main>
</body>
</html>
```